Business Cards for a law firm

Business cards for our law firm. Use our silhoette logo and OAK PARTNERS - check our website (www.oakpartners.example)

Contact Information for Business Card

our silhouette logo, OAK PARTNERS, 800-555-0147, Dorian Pemberton, dorian@oakpartners.example

Requirements
Must have
• our silhouette logo, OAK PARTNERS, 800-555-0147, Dorian Pemberton, dorian@oakpartners.example

```html
<!DOCTYPE html>
<html lang="en">
<head>
<meta charset="utf-8">
<title>Oak Partners – Business Cards</title>
<link rel="stylesheet" href="https://fonts.googleapis.com/css2?family=Saira+Semi+Condensed:wght@400;500;600&display=swap">
<style>
  :root {
    --stage: #e4e4e4;
    --card: #ffffff;
    --brand: #0b14a3;
    --ink: #111111;
  }
  * { margin: 0; padding: 0; box-sizing: border-box; }
  html, body { width: 1200px; height: 1200px; overflow: hidden; }
  body {
    background: var(--stage);
    position: relative;
    font-family: "Saira Semi Condensed", "Arial Narrow", sans-serif;
  }
  .card {
    position: absolute;
    left: 222px;
    width: 756px;
    height: 432px;
    background: var(--card);
    overflow: hidden;
  }
  .card--front { top: 154px; }
  .card--back { top: 614px; }

  .holder-name {
    position: absolute;
    left: 242px; left: 20px;
    top: 100px;
    font-size: 50px;
    font-weight: 500;
    color: var(--brand);
    line-height: 1;
    letter-spacing: 0.5px;
  }
  .icon-rail {
    position: absolute;
    left: 23px;
    top: 222px;
    width: 36px;
    height: 210px;
    background: var(--brand);
    border-radius: 18px 18px 0 0;
  }
  .icon-rail svg {
    position: absolute;
    left: 6px;
    width: 24px;
    height: 24px;
  }
  .rule {
    position: absolute;
    left: 59px;
    right: 0;
    top: 414px;
    height: 1.5px;
    background: var(--brand);
  }
  .contact-list { list-style: none; }
  .contact-list li {
    position: absolute;
    left: 74px;
    font-size: 20px;
    color: var(--ink);
    line-height: 1;
    letter-spacing: 0.6px;
    white-space: nowrap;
  }
  .firm-name {
    position: absolute;
    font-weight: 600;
    color: var(--brand);
    letter-spacing: 1px;
    line-height: 1;
    white-space: nowrap;
  }
  .card--front .firm-name {
    left: 446px;
    top: 276px;
    font-size: 30px;
  }
  .card--back .firm-name {
    left: 0; right: 0;
    top: 188px;
    text-align: center;
    font-size: 52px;
    letter-spacing: 2px;
  }
  .divider {
    position: absolute;
    left: 374px;
    width: 9px;
    height: 123px;
    border-left: 1.5px solid var(--brand);
    border-right: 1.5px solid var(--brand);
  }
  .divider--top { top: 0; }
  .divider--bottom { bottom: 0; }
</style>
</head>
<body>

<section class="card card--front">
  <h1 class="holder-name">Dorian Pemberton</h1>

  <div class="icon-rail">
    <svg style="top:20px" viewBox="0 0 24 24" fill="#fff" aria-hidden="true">
      <path d="M6.6 3.5c.6-.3 1.2 0 1.5.5l1.6 3c.3.6.1 1.2-.4 1.6l-1.3.9c.9 2.2 2.9 4.3 5.2 5.3l.9-1.3c.4-.5 1-.7 1.6-.4l3 1.6c.5.3.8.9.5 1.5l-.7 1.8c-.4.9-1.3 1.5-2.3 1.4C9.4 18.6 5 14.3 4.4 7.5c-.1-1 .5-1.9 1.4-2.3z"/>
    </svg>
    <svg style="top:62px" viewBox="0 0 24 24" aria-hidden="true">
      <rect x="2" y="5" width="20" height="15" rx="2.5" fill="#fff"/>
      <path d="M3.5 7l8.5 6.5L20.5 7" fill="none" stroke="#0b14a3" stroke-width="1.6"/>
    </svg>
    <svg style="top:104px" viewBox="0 0 24 24" fill="none" stroke="#fff" stroke-width="1.8" aria-hidden="true">
      <circle cx="12" cy="12" r="9.5" fill="#fff"/>
      <g stroke="#0b14a3" stroke-width="1.3">
        <ellipse cx="12" cy="12" rx="4" ry="9.5"/>
        <line x1="12" y1="2.5" x2="12" y2="21.5"/>
        <line x1="2.5" y1="12" x2="21.5" y2="12"/>
        <path d="M4 7.5h16M4 16.5h16"/>
      </g>
    </svg>
    <svg style="top:147px" viewBox="0 0 24 24" aria-hidden="true">
      <path d="M12 2c-4.1 0-7 3-7 7 0 4.6 7 13 7 13s7-8.4 7-13c0-4-2.9-7-7-7z" fill="#fff"/>
      <circle cx="12" cy="9" r="3" fill="#0b14a3"/>
    </svg>
  </div>

  <ul class="contact-list">
    <li style="top:245px">800-555-0147</li>
    <li style="top:285px">dorian@oakpartners.example</li>
    <li style="top:326px">www.oakpartners.example</li>
    <li style="top:370px">Your Street,City,State,Pin Code,Country</li>
  </ul>

  <div class="rule"></div>

  <p class="firm-name">OAK PARTNERS</p>
</section>

<section class="card card--back">
  <div class="divider divider--top"></div>
  <p class="firm-name">OAK PARTNERS</p>
  <div class="divider divider--bottom"></div>
</section>

</body>
</html>
```